Custom Cabinet Shop Needs a website design

Hi,
We need a website for a Custom Cabinet Shop and Cabinet parts manufacturing business.
The business has two sides to it. One side provides custom Kitchens, vanities, entertainment units, offices and what not to homeowners and contractors.
The 2nd side of the business provides built to order cabinet boxes and other parts required to put together a project to other cabinet shops, small contractors looking to install there own cabinets.
Website will need a Gallery to display work.
Color scheme to go well with logo.
current website is www.brambleoakcustomcabinets.com
being changed to www.brambleoak.ca
Logo Included in attached files.
Tagline "Joinery with Spirit"
Mission Statement "Our passion is to deliver inspired cabinetry solutions to suit all your needs, supported by our phenomenal star class customer service"
The website should convey quality and professionalism.
Thank you.
Homeowners/ Contractors
Entertainment

```html
<!DOCTYPE html>
<html lang="en">
<head>
<meta charset="utf-8">
<title>Brambleoak Custom Cabinets</title>
<link rel="stylesheet" href="https://fonts.googleapis.com/css2?family=Open+Sans:wght@400;600;700&display=swap">
<style>
:root{
  --black:#000;
  --orange:#e63b1a;
  --brown:#3a2e27;
  --caption:rgba(96,78,62,.62);
  --cream:#f3eedb;
  --amber:#df8a12;
  --tangerine:#ea6a22;
  --green:#5e9617;
  --white:#fff;
  --ink:#1d1d1d;
}
*{box-sizing:border-box;margin:0;padding:0}
html,body{width:1200px;height:2302px;overflow:hidden}
body{position:relative;font-family:"Open Sans",Arial,sans-serif;background:var(--cream);color:var(--ink)}
.abs{position:absolute}
.site-header{left:0;top:0;width:1200px;height:126px;background:var(--black);display:flex;align-items:center;justify-content:center}
.brand{display:flex;align-items:center;gap:14px;color:var(--white);font-weight:700;font-size:34px;letter-spacing:1px;text-transform:uppercase}
.brand-mark{width:22px;height:22px;background:var(--orange)}
.main-nav{left:0;top:126px;width:1200px;height:58px;background:var(--orange)}
.main-nav a{position:absolute;top:0;height:58px;line-height:58px;color:var(--white);text-decoration:none;font-size:17px;text-transform:uppercase;transform:translateX(-50%)}
.main-nav .is-active{left:98px;width:98px;transform:none;background:var(--black);text-align:center}
.nav-caret{left:305px;top:40px}
.hero{left:0;top:184px;width:1200px;height:542px;background:linear-gradient(100deg,#d9d6d0 0%,#bfb9b1 30%,#6f6156 55%,#c8a777 80%,#e9e4d9 100%)}
.hero-caption{left:698px;top:427px;width:401px;height:103px;background:var(--caption);color:#111;font-weight:700;font-size:27px;display:flex;align-items:center;justify-content:center}
.round-btn{width:54px;height:54px;border-radius:50%;background:var(--white);display:flex;align-items:center;justify-content:center}
.intro{left:0;top:726px;width:1200px;height:804px;background:var(--brown);color:var(--white)}
.intro-photo{left:109px;top:799px;width:168px;height:168px;border-radius:50%;border:2px solid #ddd;background:radial-gradient(circle at 40% 50%,#a86a33,#3d3128 70%)}
.intro-title{left:318px;top:803px;width:650px;text-align:center;font-size:26px;font-weight:400;color:var(--white)}
.intro-text{left:318px;top:848px;width:660px;font-size:16px;line-height:26px;color:var(--white)}
.more-btn{left:571px;top:973px;width:64px;height:64px;border-radius:50%;background:var(--white);color:var(--ink);font-size:16px;font-weight:600;display:flex;align-items:center;justify-content:center}
.section-title{left:0;width:1200px;text-align:center;font-size:25px;font-weight:700;text-transform:uppercase}
.gallery-tile{top:1191px;width:334px;height:339px}
.tile-label{position:absolute;left:0;width:334px;height:74px;display:flex;align-items:center;justify-content:center;color:var(--white);font-size:21px;text-transform:uppercase}
.tile-photo{position:absolute;left:0;width:334px;height:265px}
.gallery-arrow{top:1323px;width:54px;height:74px;background:rgba(40,30,25,.75);display:flex;align-items:center;justify-content:center}
.service-card{width:473px;height:213px}
.service-photo{position:absolute;left:0;top:0;width:237px;height:213px;clip-path:polygon(0 0,100% 0,100% 80%,0 100%)}
.service-body{position:absolute;left:237px;top:0;width:236px;height:213px;background:var(--white);text-align:center;padding-top:24px}
.service-body h3{font-size:22px;font-weight:600;margin-bottom:14px}
.service-body p{font-size:13px;line-height:20.5px;padding:0 26px;height:82px}
.service-body .more{display:inline-flex;align-items:center;gap:6px;margin-top:14px;font-size:16px;font-weight:600}
.top-btn{left:950px;top:2171px;width:64px;height:64px;border-radius:50%;background:var(--green);color:var(--white);font-size:15px;font-weight:700;display:flex;align-items:center;justify-content:center}
.site-footer{left:0;top:2249px;width:1200px;height:53px;background:var(--white);border-top:1px solid #ccc}
.social{top:15px;width:22px;height:22px;border-radius:4px}
.footer-note{left:0;top:16px;width:1170px;text-align:center;font-size:12px}
</style>
</head>
<body>
<header class="site-header abs">
  <div class="brand"><span class="brand-mark"></span>Brambleoak</div>
</header>
<nav class="main-nav abs">
  <a class="is-active" href="#">Home</a>
  <a style="left:313px" href="#">About Us</a>
  <a style="left:493px" href="#">Gallery</a>
  <a style="left:678px" href="#">Services</a>
  <a style="left:873px" href="#">Warranty</a>
  <a style="left:1059px" href="#">Contact</a>
  <svg class="nav-caret abs" width="16" height="9" viewBox="0 0 16 9"><path d="M0 0h16L8 9z" fill="#000"/></svg>
</nav>
<section class="hero abs" role="img" aria-label="Modern bathroom with freestanding tub, red towels and wall-mounted vanity mirror"></section>
<div class="hero-caption abs">Joinery with Spirit</div>
<div class="round-btn abs" style="left:549px;top:691px"><svg width="18" height="22" viewBox="0 0 18 22"><path d="M13 2L4 11l9 9" stroke="#111" stroke-width="4" fill="none"/></svg></div>
<div class="round-btn abs" style="left:605px;top:691px"><svg width="18" height="22" viewBox="0 0 18 22"><path d="M5 2l9 9-9 9" stroke="#111" stroke-width="4" fill="none"/></svg></div>

<section class="intro abs"></section>
<div class="intro-photo abs" role="img" aria-label="Live-edge wood counter against a stone wall"></div>
<h1 class="intro-title abs">Welcome to Our Site !</h1>
<p class="intro-text abs">Our passion is to deliver inspired cabinetry solutions to suit all your needs, supported by our phenomenal star class customer service</p>
<div class="more-btn abs">More</div>
<h2 class="section-title abs" style="top:1117px;color:#fff">Gallery</h2>

<div class="gallery-tile abs" style="left:98px">
  <div class="tile-photo" style="top:0;background:linear-gradient(90deg,#2a2a2e,#d8d2c8 40%,#cfc8bd 60%,#1f1f24)" role="img" aria-label="Dark built-in cabinets framing a fireplace"></div>
  <div class="tile-label" style="top:265px;background:var(--tangerine)">Comfort</div>
</div>
<div class="gallery-tile abs" style="left:432px">
  <div class="tile-label" style="top:0;background:var(--amber);color:#3a2e27">Quality</div>
  <div class="tile-photo" style="top:74px;background:linear-gradient(135deg,#4a4038,#a8652e 50%,#6b5a45)" role="img" aria-label="Live-edge wood counter with stone wall"></div>
</div>
<div class="gallery-tile abs" style="left:766px">
  <div class="tile-photo" style="top:0;background:linear-gradient(180deg,#e8e6e2,#3b2a22 30%,#5a3a2c 80%,#2a1e18)" role="img" aria-label="Dark wood display cabinet with drawers"></div>
  <div class="tile-label" style="top:265px;background:var(--green)">Philosophy</div>
</div>
<div class="gallery-arrow abs" style="left:98px"><svg width="14" height="20" viewBox="0 0 14 20"><path d="M11 2L3 10l8 8" stroke="#fff" stroke-width="3" fill="none"/></svg></div>
<div class="gallery-arrow abs" style="left:1047px"><svg width="14" height="20" viewBox="0 0 14 20"><path d="M3 2l8 8-8 8" stroke="#fff" stroke-width="3" fill="none"/></svg></div>

<h2 class="section-title abs" style="top:1569px">Our Services</h2>

<article class="service-card abs" style="left:98px;top:1647px">
  <div class="service-photo" style="background:linear-gradient(135deg,#5a8a8c,#d8d4cc 60%,#8a6a4a)" role="img" aria-label="Laundry room with cabinets and washer and dryer"></div>
  <div class="service-body"><h3>Kitchens</h3><p>Custom kitchens built to your plan, from the first sketch to the final fitted door.</p><span class="more">More <svg width="12" height="12" viewBox="0 0 12 12"><circle cx="6" cy="6" r="6" fill="#1d1d1d"/><path d="M5 3l3 3-3 3" stroke="#fff" stroke-width="1.6" fill="none"/></svg></span></div>
</article>
<article class="service-card abs" style="left:628px;top:1647px">
  <div class="service-photo" style="background:linear-gradient(135deg,#3a2a30,#7a1e34 50%,#d9d9d9)" role="img" aria-label="Kitchen with burgundy gloss cabinets"></div>
  <div class="service-body"><h3>Vanities</h3><p>Bathroom vanities and storage made to measure for homeowners and contractors alike.</p><span class="more">More <svg width="12" height="12" viewBox="0 0 12 12"><circle cx="6" cy="6" r="6" fill="#1d1d1d"/><path d="M5 3l3 3-3 3" stroke="#fff" stroke-width="1.6" fill="none"/></svg></span></div>
</article>
<article class="service-card abs" style="left:98px;top:1896px">
  <div class="service-photo" style="background:linear-gradient(135deg,#e8891a,#f3f0ea 55%,#e86a10)" role="img" aria-label="Kitchen with orange cabinets"></div>
  <div class="service-body"><h3>Media Units</h3><p>Entertainment units and home offices crafted to fit the room and the way you live.</p><span class="more">More <svg width="12" height="12" viewBox="0 0 12 12"><circle cx="6" cy="6" r="6" fill="#1d1d1d"/><path d="M5 3l3 3-3 3" stroke="#fff" stroke-width="1.6" fill="none"/></svg></span></div>
</article>
<article class="service-card abs" style="left:628px;top:1896px">
  <div class="service-photo" style="background:linear-gradient(135deg,#c41c1c,#8a8680 45%,#b81818)" role="img" aria-label="Kitchen with red cabinets and island"></div>
  <div class="service-body"><h3>Cabinet Parts</h3><p>Built to order boxes and parts for cabinet shops and installers doing their own work.</p><span class="more">More <svg width="12" height="12" viewBox="0 0 12 12"><circle cx="6" cy="6" r="6" fill="#1d1d1d"/><path d="M5 3l3 3-3 3" stroke="#fff" stroke-width="1.6" fill="none"/></svg></span></div>
</article>

<div class="top-btn abs">TOP</div>

<footer class="site-footer abs">
  <span class="social abs" style="left:101px;background:var(--orange)"></span>
  <span class="social abs" style="left:158px;background:#222"></span>
  <span class="social abs" style="left:215px;background:var(--green)"></span>
  <span class="social abs" style="left:271px;background:var(--amber)"></span>
  <p class="footer-note abs">brambleoakcustomcabinets © 2015 • Privacy Policy</p>
</footer>
</body>
</html>
```